Letter and Envelope Design For Harborline Realty

Please design a letter and an envelope incorporating our logo (See Attached). We are also launched a business card contest. Since we want them to match, please feel free to submit a design for both the business card and also the letter design and envelope.

Requirements
Must have
• The envelope, the letter and the business cards must match somehow connecting the designs. We want them to have something that holds them together besides the logo.

```html
<!DOCTYPE html>
<html lang="en">
<head>
<meta charset="utf-8">
<title>Harborline Realty Stationery</title>
<link href="https://fonts.googleapis.com/css2?family=Source+Sans+3:wght@400;600;700&display=swap" rel="stylesheet">
<style>
  :root{
    --navy:#283080;
    --slate:#5a5a5a;
    --ink:#444444;
    --paper:#ffffff;
    --canvas:#ffffff;
  }
  *{box-sizing:border-box;margin:0;padding:0}
  html,body{width:1200px;height:970px;overflow:hidden;background:var(--canvas)}
  body{position:relative;font-family:"Source Sans 3",sans-serif;color:var(--ink)}
  .piece{position:absolute;background:var(--paper);box-shadow:0 4px 18px rgba(0,0,0,.18)}
  .abs{position:absolute}

  /* brand mark: plain circle + wordmark */
  .brand-ring{position:absolute;border-radius:50%;border:2.5px solid var(--navy);background:var(--paper)}
  .wordmark{position:absolute;transform:translateX(-50%);text-align:center;color:var(--navy);font-weight:600;white-space:nowrap;line-height:1}
  .wordmark span{display:block}

  /* contact list */
  .rule{position:absolute;width:1px;background:#9a9a9a}
  .contact{position:absolute;display:flex;align-items:center;white-space:nowrap;color:var(--ink)}
  .contact svg{flex:none;background:var(--navy);fill:none;stroke:#fff;stroke-width:1.4}

  /* linking band */
  .band{position:absolute;left:0;right:0}
  .band .navy{position:absolute;left:0;top:0;bottom:0;background:var(--navy)}
  .band .slate{position:absolute;right:0;top:0;bottom:0;background:var(--slate)}
  .band-ring{position:absolute;border-radius:50%;background:var(--paper);border:3px solid var(--navy);box-shadow:0 0 0 3px var(--paper)}

  /* letterhead */
  .letterhead{left:18px;top:78px;width:594px;height:826px}
  /* business card */
  .card-front{left:629px;top:78px;width:405px;height:237px;background:var(--navy)}
  .card-back{left:629px;top:321px;width:405px;height:237px}
  .card-name{position:absolute;left:203px;top:33px;font-size:19px;font-weight:700;color:var(--navy)}
  .card-role{position:absolute;left:203px;top:55px;font-size:13.5px;color:var(--ink)}
  /* envelope */
  .envelope{left:629px;top:600px;width:525px;height:318px;background:none;box-shadow:none}
  .envelope-body{position:absolute;left:0;top:70px;width:525px;height:248px;background:var(--paper);box-shadow:0 4px 18px rgba(0,0,0,.18)}
</style>
</head>
<body>

<svg width="0" height="0" style="position:absolute" aria-hidden="true">
  <defs>
    <symbol id="ic-pin" viewBox="0 0 16 16"><path d="M8 3.5a3 3 0 0 1 3 3c0 2.2-3 5.5-3 5.5S5 8.7 5 6.5a3 3 0 0 1 3-3z"/><circle cx="8" cy="6.5" r="1"/></symbol>
    <symbol id="ic-phone" viewBox="0 0 16 16"><path d="M3.5 6.5c0-1.5 2-2.5 4.5-2.5s4.5 1 4.5 2.5l-1.8.4-.4-1.2H5.7l-.4 1.2z" fill="#fff" stroke="none"/><rect x="4.5" y="7.5" width="7" height="4.5" rx="1" fill="#fff" stroke="none"/></symbol>
    <symbol id="ic-mail" viewBox="0 0 16 16"><rect x="3.5" y="5" width="9" height="6.5"/><path d="M3.5 5l4.5 3.8L12.5 5"/></symbol>
    <symbol id="ic-globe" viewBox="0 0 16 16"><circle cx="8" cy="8" r="4.5"/><ellipse cx="8" cy="8" rx="2" ry="4.5"/><path d="M3.5 8h9"/></symbol>
  </defs>
</svg>

<!-- Letterhead -->
<section class="piece letterhead">
  <div class="brand-ring" style="left:80px;top:26px;width:64px;height:64px"></div>
  <div class="wordmark" style="left:112px;top:96px">
    <span style="font-size:19px;letter-spacing:3px">HARBORLINE</span>
    <span style="font-size:13px;letter-spacing:6px;margin-top:5px">REALTY</span>
  </div>

  <div class="rule" style="left:401px;top:40px;height:72px"></div>
  <div class="contact" style="left:414px;top:40px;font-size:9.5px;gap:9px"><svg width="11" height="11"><use href="#ic-pin"/></svg>Harborline Realty</div>
  <div class="contact" style="left:414px;top:58px;font-size:9.5px;gap:9px"><svg width="11" height="11"><use href="#ic-phone"/></svg>555-014-2286</div>
  <div class="contact" style="left:414px;top:77px;font-size:9.5px;gap:9px"><svg width="11" height="11"><use href="#ic-mail"/></svg>info@harborline-realty.com</div>
  <div class="contact" style="left:414px;top:95px;font-size:9.5px;gap:9px"><svg width="11" height="11"><use href="#ic-globe"/></svg>www.harborline-realty.com</div>

  <div class="band" style="top:765px;height:19px">
    <div class="navy" style="width:270px"></div>
    <div class="slate" style="width:268px"></div>
  </div>
  <div class="band-ring" style="left:272px;top:749px;width:52px;height:52px"></div>
</section>

<!-- Business card, front -->
<section class="piece card-front">
  <div class="brand-ring" style="left:170px;top:87px;width:64px;height:64px;background:none;border-color:#fff"></div>
  <div class="wordmark" style="left:202px;top:160px;color:#fff;font-size:11px;letter-spacing:3px">HARBORLINE REALTY</div>
  <div class="abs" style="left:0;right:0;top:205px;text-align:center;color:#fff;font-size:12.5px">www.harborline-realty.com</div>
</section>

<!-- Business card, back -->
<section class="piece card-back">
  <div class="brand-ring" style="left:65px;top:64px;width:52px;height:52px"></div>
  <div class="wordmark" style="left:91px;top:122px">
    <span style="font-size:15px;letter-spacing:2.5px">HARBORLINE</span>
    <span style="font-size:11px;letter-spacing:5px;margin-top:3px">REALTY</span>
  </div>

  <div class="rule" style="left:191px;top:33px;height:142px"></div>
  <div class="card-name">Daniel Reyes</div>
  <div class="card-role">Realtor</div>
  <div class="contact" style="left:209px;top:96px;font-size:12.5px;gap:10px"><svg width="15" height="15"><use href="#ic-pin"/></svg>Harborline Realty</div>
  <div class="contact" style="left:209px;top:117px;font-size:12.5px;gap:10px"><svg width="15" height="15"><use href="#ic-phone"/></svg>555-014-2286</div>
  <div class="contact" style="left:209px;top:139px;font-size:12.5px;gap:10px"><svg width="15" height="15"><use href="#ic-mail"/></svg>info@harborline-realty.com</div>
  <div class="contact" style="left:209px;top:161px;font-size:12.5px;gap:10px"><svg width="15" height="15"><use href="#ic-globe"/></svg>www.harborline-realty.com</div>

  <div class="band" style="top:209px;height:12px">
    <div class="navy" style="width:178px"></div>
    <div class="slate" style="width:191px"></div>
  </div>
  <div class="band-ring" style="left:178px;top:196px;width:34px;height:34px;border-width:2px"></div>
</section>

<!-- Envelope -->
<section class="piece envelope">
  <svg class="abs" style="left:0;top:0" width="525" height="71" aria-hidden="true">
    <path d="M0 71 L20 12 Q24 0 38 0 L487 0 Q501 0 505 12 L525 71 Z" fill="var(--navy)"/>
  </svg>
  <div class="envelope-body">
    <div class="brand-ring" style="left:51px;top:15px;width:42px;height:42px;border-width:2px"></div>
    <div class="wordmark" style="left:72px;top:61px">
      <span style="font-size:12px;letter-spacing:2px">HARBORLINE</span>
      <span style="font-size:8.5px;letter-spacing:4px;margin-top:3px">REALTY</span>
    </div>

    <div class="rule" style="left:388px;top:23px;height:49px"></div>
    <div class="contact" style="left:397px;top:23px;font-size:7.5px;gap:8px"><svg width="9" height="9"><use href="#ic-pin"/></svg>Harborline Realty</div>
    <div class="contact" style="left:397px;top:36px;font-size:7.5px;gap:8px"><svg width="9" height="9"><use href="#ic-phone"/></svg>555-014-2286</div>
    <div class="contact" style="left:397px;top:49px;font-size:7.5px;gap:8px"><svg width="9" height="9"><use href="#ic-mail"/></svg>info@harborline-realty.com</div>
    <div class="contact" style="left:397px;top:63px;font-size:7.5px;gap:8px"><svg width="9" height="9"><use href="#ic-globe"/></svg>www.harborline-realty.com</div>

    <div class="band" style="top:224px;height:15px">
      <div class="navy" style="width:243px"></div>
      <div class="slate" style="width:244px"></div>
    </div>
    <div class="band-ring" style="left:240px;top:210px;width:42px;height:42px;border-width:2px"></div>
  </div>
</section>

</body>
</html>
```